House Cleaning Platform for Consumers and Cleaners

UPDATE: I've attached screenshots showing a purchase flow example, something all designers have missed in their designs. PLEASE check the URLs I've included in the brief for examples of a cleaning website. I've seen mostly landing pages and nothing else.

WHAT I'M LOOKING FOR:
I need the UI designed for a house cleaning web platform from 2 separate experiences: one from the consumer end to order a cleaner to come clean their house and one from a cleaner’s end that manages their orders and manages their schedule.

The UI will need to include photo uploading for before and after photos, a checkout/cart experience w/ tips, toggle options for adding and removing rooms/extras cleaning add-ons, customer+cleaner reviews (meaning the cleaner finished the job and they can rate and review the customer as well as the customer can rate and review the cleaner), order history for consumers, job history for cleaners, profile, settings, and landing pages for both.

PLEASE DO NOT USE THE COLOR BLUE AS THE PRIMARY COLOR. Use a light green (HEX #2fdf86) instead for primary theming color.

REFERENCES:
If you'd like a few websites I've enjoyed for references, checkout:
larkpolish.example, vomby.example, and brightfernhome.example.

For sake of branding, the company name is PlumNest. Currently do not have a logo as we have not decided on the name. Logo will come later.

Feel free to reach out to me if you have any questions!
Updates

Most designer submissions were a landing page and only a landing page. Very few designed the flows I requested and none designed a schedule management page. I even updated the Brief to more clearly outline the needs and references. Only about 2-3 of the designers actually did more than a landing page. Still don't believe I received 6 designers input that I had paid for.

Target Market(s)

FULL-TIME WORKING HOUSEHOLDS, SINGLE PROFESSIONALS, SINGLE PARENTS, ELDERLY & MOBILITY CHALLENGED, BUSY BODIES.

Industry/Entity Type

Cleaning, gig work.

Number of Pages Required

5+ page

Font styles to use
Other font styles liked:
• Jost or Lexend are great Google Font options I've used in the pitch deck and horribly done app mockups.

Colors
00AB8E
00BBA5
67D7C9
C6EFE9
E9F9F6
59FF00
82FF00
B8FF75
E3FFCB
F4FFEA
FFF300
FFF600
FEFA6F
FFFEC7
FFFEE8
FFC000
F8CF3A
FAE287
FDF2CF
FEFAEE

Requirements
Must have
• Landing page, consumer flow, cleaner schedule management, checkout flow, Rate & Review for consumer and/or cleaner, order history, profile.
Nice to have
• I'd like it to be simple in design and modern, but not so simple it's boring. Iconography can sometimes break that up, but I don't want it looking busy. It's a cleaning platform so the UI should look clean.

```html
<!DOCTYPE html>
<html lang="en">
<head>
<meta charset="utf-8">
<title>PlumNest – Book Your Services Now</title>
<link rel="stylesheet" href="https://fonts.googleapis.com/css2?family=Lexend:wght@400;500;700&family=Noto+Sans:wght@500;600;700&family=Nunito:wght@400;500;600&display=swap">
<style>
  :root {
    --green: #26d07c;
    --orange: #f7931e;
    --ink: #111111;
    --muted: #444444;
    --placeholder: #b4b4b4;
    --line: #d9d9d9;
    --field-border: #cfcfcf;
    --bg: #ffffff;
    --ui: "Lexend", sans-serif;
    --head: "Noto Sans", sans-serif;
    --body: "Nunito", sans-serif;
  }
  * { box-sizing: border-box; margin: 0; padding: 0; }
  html, body { width: 1200px; height: 949px; overflow: hidden; background: var(--bg); }
  body { position: relative; font-family: var(--body); color: var(--ink); }
  .abs { position: absolute; }

  /* Header */
  .brand { left: 101px; top: 18px; font-family: var(--ui); font-weight: 700; font-size: 30px; color: var(--green); letter-spacing: -0.3px; }
  .nav a { position: absolute; top: 27px; font-family: var(--ui); font-size: 11.5px; color: var(--ink); text-decoration: none; }
  .search { left: 731px; top: 22px; width: 218px; height: 25px; border: 1px solid var(--line); border-radius: 13px; display: flex; align-items: center; padding-left: 8px; gap: 14px; font-family: var(--ui); font-size: 11.5px; }
  .login { left: 981px; top: 27px; font-family: var(--ui); font-size: 11.5px; }
  .signup { left: 1024px; top: 22px; width: 74px; height: 25px; border-radius: 13px; background: var(--green); font-family: var(--ui); font-size: 10.5px; display: flex; align-items: center; justify-content: center; }

  /* Title & stepper */
  .page-title { left: 0; width: 1204px; top: 128px; text-align: center; font-family: var(--head); font-weight: 700; font-size: 37px; letter-spacing: -0.2px; }
  .stepper { left: 0; top: 0; }

  /* Payment method */
  .section-title { left: 101px; top: 280px; font-family: var(--head); font-weight: 500; font-size: 20px; }
  .section-sub { left: 101px; top: 321px; font-size: 11.5px; color: var(--muted); }
  .method { top: 370px; width: 170px; height: 56px; border: 1px solid var(--field-border); display: flex; align-items: center; padding-left: 12px; gap: 19px; font-family: var(--head); font-weight: 500; font-size: 16px; }
  .method.is-active { border-color: var(--green); }
  .method-mark { width: 30px; height: 26px; border-radius: 3px; }

  .field-label { left: 101px; font-size: 13px; }
  .field { border: 1px solid var(--field-border); height: 38px; display: flex; align-items: center; padding-left: 18px; font-size: 11.5px; color: var(--placeholder); }

  .book-btn { left: 101px; top: 768px; width: 174px; height: 49px; border-radius: 25px; background: var(--green); font-family: var(--ui); font-weight: 500; font-size: 15.5px; display: flex; align-items: center; justify-content: center; }
  .terms { left: 101px; top: 823px; width: 460px; font-size: 11.5px; line-height: 18px; color: var(--muted); }

  /* Summary */
  .summary { left: 807px; top: 266px; width: 291px; height: 268px; border: 1px solid var(--line); border-radius: 10px; }
  .summary-title { position: absolute; top: 33px; width: 100%; text-align: center; font-family: var(--head); font-weight: 500; font-size: 20px; }
  .row { position: absolute; left: 0; width: 100%; }
  .row .k { position: absolute; right: 136px; white-space: nowrap; }
  .row .v { position: absolute; left: 205px; white-space: nowrap; }
  .row.main { font-family: var(--head); font-weight: 500; font-size: 15.5px; }
  .row.minor { font-family: var(--head); font-size: 11px; }
  .divider { position: absolute; left: 31px; width: 229px; top: 196px; border-top: 1px solid var(--line); }
  .total-v { color: var(--orange); }
</style>
</head>
<body>
  <header>
    <div class="abs brand">PlumNest</div>
    <nav class="nav">
      <a style="left:438px">Home</a>
      <a style="left:489px">Pricing</a>
      <a style="left:546px">Services</a>
      <a style="left:612px">Contact</a>
      <a style="left:674px">Help</a>
    </nav>
    <div class="abs search">
      <svg width="14" height="14" viewBox="0 0 14 14" fill="none" stroke="#222" stroke-width="1.1"><circle cx="6" cy="6" r="5"/><line x1="9.6" y1="9.6" x2="13" y2="13"/></svg>
      <span>Search</span>
    </div>
    <div class="abs login">Login</div>
    <div class="abs signup">Sign Up</div>
  </header>

  <h1 class="abs page-title">Book Your Services Now</h1>

  <svg class="abs stepper" width="1200" height="240" viewBox="0 0 1200 240" aria-hidden="true">
    <line x1="186" y1="216" x2="1015" y2="216" stroke="#dcdcdc" stroke-width="3"/>
    <g fill="#fff" stroke="#d6d6d6" stroke-width="1.6">
      <circle cx="174" cy="216" r="12"/>
      <circle cx="344" cy="216" r="12"/>
      <circle cx="515" cy="216" r="12"/>
      <circle cx="686" cy="216" r="12"/>
      <circle cx="856" cy="216" r="12"/>
    </g>
    <circle cx="1027" cy="216" r="12" fill="#fff" stroke="#f7931e" stroke-width="1.8"/>
  </svg>

  <main>
    <h2 class="abs section-title">Select Payment Method</h2>
    <p class="abs section-sub">Your card will not be charged until the day of service.</p>

    <div class="abs method is-active" style="left:101px"><span class="method-mark" style="background:#f8c23a"></span>Credit Card</div>
    <div class="abs method" style="left:283px"><span class="method-mark" style="background:#2fa6c9"></span>Debit Card</div>
    <div class="abs method" style="left:465px"><span class="method-mark" style="background:#3f87b0"></span>Orbit Card</div>

    <label class="abs field-label" style="top:459px">Name On Card</label>
    <div class="abs field" style="left:101px;top:490px;width:469px">Name</div>

    <label class="abs field-label" style="top:548px">Credit Card Details</label>
    <div class="abs field" style="left:101px;top:579px;width:469px;gap:14px">
      <svg width="13" height="10" viewBox="0 0 13 10" fill="none" stroke="#f7931e" stroke-width="0.9"><rect x="0.5" y="0.5" width="12" height="9" rx="1"/><circle cx="4" cy="4" r="1.4"/><path d="M2 8c.5-1.5 3.5-1.5 4 0M7.5 3.5h3.5M7.5 5.5h3.5"/></svg>
      <span>Card Number</span>
    </div>

    <label class="abs field-label" style="top:637px;left:101px">Month</label>
    <label class="abs field-label" style="top:637px;left:267px">Year</label>
    <label class="abs field-label" style="top:637px;left:434px">CVV</label>
    <div class="abs field" style="left:101px;top:667px;width:135px">Month</div>
    <div class="abs field" style="left:267px;top:667px;width:135px">Year</div>
    <div class="abs field" style="left:434px;top:667px;width:135px">CVV</div>

    <div class="abs book-btn">Book Now</div>
    <p class="abs terms">*By clicking confirm booking you are agreeing to our friendly privacy policy and booking terms and conditions.</p>
  </main>

  <aside class="abs summary">
    <div class="summary-title">Payment Details:</div>
    <div class="row main" style="top:93px"><span class="k">Cleaning Price:</span><span class="v">$350</span></div>
    <div class="row minor" style="top:123px"><span class="k">15% Discount:</span><span class="v">$47.27</span></div>
    <div class="row minor" style="top:147px"><span class="k">Coupon Code Discount:</span><span class="v">$00.00</span></div>
    <div class="row minor" style="top:172px"><span class="k">Gift Code Discount:</span><span class="v">$00.00</span></div>
    <div class="divider"></div>
    <div class="row main" style="top:215px;font-size:16px"><span class="k">Total Price:</span><span class="v total-v">$302.75</span></div>
  </aside>
</body>
</html>
```